tinyTally Resource Book - 10 maths tasks to do outside

I need a 22 (11 pages back to back) page A6 sized book produced to standard for submission to professional printer. Needs to be as .pdf file showing guide lines and allowances for colour bleed. I have text already written and submitted as attachment in a Word file with margins set to A6 size. The theme of the materials is "Nature Play" so using lots of pictures from nature (Australia preferably) and showing lots of patterns in nature (rocks, leaves, flower petals etc). Some of the tasks refer to specific activities, such as "shadows" and "floating" so would be great to illustrate appropriately. The big emphasis is on learning outside the classroom, getting kids to engage actively with nature. I would like to see the pages as full colour - so not white background. The book itself will be spiral bound along the top edge so a margin of at least 1cm will be required at the top of each page (or the bottom of even numbered pages). Book will be printed on plastic laminated matte paper for outdoor use. Font size needs to be big enough to read. Fonts sizes, alignments and page numbers are all different at the moment and need to be standardised. One photo is included in a page as a sample if you can use it, otherwise disregard. Logo for Wattlebrook Numeracy Guild is also included to have as part of the acknowledgements at the back of the book.

Target Market(s)

Book is for early childhood and preschool teachers.

Industry/Entity Type

Education

Font styles to use
Sans Serif

Requirements
Must have
• Colour and appeal.
Nice to have
• Use of natural colours instead of bright catchy colours but that is your call.
Should not have
• American spelling

```html
<!DOCTYPE html>
<html lang="en-AU">
<head>
<meta charset="utf-8">
<title>Big Bigger Biggest – tinyTally Resource Book</title>
<link rel="stylesheet" href="https://fonts.googleapis.com/css2?family=Nunito:wght@900&family=Didact+Gothic&display=swap">
<style>
  :root {
    --paper: #ffffff;
    --ink-heading: #2f3d8f;
    --ink-body: #2b2730;
    --bullet-red: #d8232a;
    --sky: #7f9ec9;
    --sea: #9fb7d8;
    --shore: #d9d6cf;
    --sand: #c9ad8c;
    --sand-deep: #b89a78;
    --trim: #1a1a1a;
  }
  * { margin: 0; padding: 0; box-sizing: border-box; }
  html, body { width: 964px; height: 1200px; overflow: hidden; background: var(--paper); }
  .sheet { position: relative; width: 964px; height: 1200px; }
  .crop-marks { position: absolute; inset: 0; }
  .page {
    position: absolute; left: 56px; top: 56px; width: 850px; height: 1090px; overflow: hidden;
  }
  .page-photo {
    position: absolute; inset: 0;
    background: linear-gradient(180deg, var(--sky) 0%, var(--sea) 30%, var(--shore) 44%, var(--sand) 52%, var(--sand) 80%, var(--sand-deep) 100%);
  }
  .section-heading, .task-list { position: absolute; left: 76px; }
  .section-heading {
    font-family: "Nunito", "Arial Rounded MT Bold", sans-serif;
    font-weight: 900; font-size: 54px; line-height: 62px; color: var(--ink-heading);
    letter-spacing: 0.5px;
    text-shadow: 2px 0 0 #fff, -2px 0 0 #fff, 0 2px 0 #fff, 0 -2px 0 #fff,
                 2px 2px 0 #fff, -2px -2px 0 #fff, 2px -2px 0 #fff, -2px 2px 0 #fff,
                 3px 3px 3px rgba(0,0,0,0.35);
  }
  .task-list {
    left: 156px; list-style: none;
    font-family: "Didact Gothic", "Century Gothic", sans-serif;
    font-size: 32px; line-height: 42.4px; color: var(--ink-body);
  }
  .task-list li { position: relative; }
  .task-list li::before {
    content: ""; position: absolute; left: -22px; top: 12px;
    width: 17px; height: 17px; background: var(--bullet-red); transform: rotate(45deg);
  }
  .title { top: 143px; }
  .steps { top: 202px; }
  .prompts-heading { top: 463px; }
  .prompts { top: 524px; }
  .variations-heading { top: 699px; }
  .variations { top: 760px; }
  .ideas-heading { top: 849px; }
  .ideas { top: 912px; }
</style>
</head>
<body>
<div class="sheet">
  <svg class="crop-marks" width="964" height="1200" viewBox="0 0 964 1200" aria-hidden="true">
    <g stroke="var(--trim)" stroke-width="1" fill="none">
      <path d="M57 0V38M80 0V38M0 53H38M0 75H38"/>
      <path d="M57 75H80V53"/>
      <path d="M907 0V38M884 0V38M964 53H926M964 75H926"/>
      <path d="M907 75H884V53"/>
      <path d="M57 1200V1162M80 1200V1162M0 1147H38M0 1125H38"/>
      <path d="M57 1125H80V1147"/>
      <path d="M907 1200V1162M884 1200V1162M964 1147H926M964 1125H926"/>
      <path d="M907 1125H884V1147"/>
    </g>
  </svg>

  <main class="page">
    <div class="page-photo" role="img" aria-label="Photograph of a calm beach with blue sea behind and a stack of three smooth white pebbles resting on the sand"></div>

    <h1 class="section-heading title">2. Big Bigger Biggest</h1>
    <ul class="task-list steps">
      <li>Find an object – stone, leaf, stick etc</li>
      <li>Now find a bigger one</li>
      <li>Now find an even bigger one than<br>that</li>
      <li>Line them up – big bigger biggest</li>
      <li>Keep adding to your line</li>
    </ul>

    <h2 class="section-heading prompts-heading">Prompting questions</h2>
    <ul class="task-list prompts">
      <li>Where do you put new rocks in the<br>line?</li>
      <li>Can you take away some rocks to<br>make your “biggest” the “smallest”?</li>
    </ul>

    <h2 class="section-heading variations-heading">Variations</h2>
    <ul class="task-list variations">
      <li>Small Smaller Smallest</li>
      <li>Long Longer Longest</li>
    </ul>

    <h2 class="section-heading ideas-heading">Big Ideas</h2>
    <ul class="task-list ideas">
      <li>Comparison</li>
      <li>Visualisation</li>
      <li>Prediction</li>
    </ul>
  </main>
</div>
</body>
</html>
```